Advertising company unique advertising platform

we need a logo design for a new company based in Australia Melbourne. We develop innovated advertising platform where consumer can use this platform to get regular discount, as business owner they can use this platform for free advertisement. Payment for this advertisement platform only payable every two weeks, when I generate revenue for their business

Industry/Entity Type

Advertising

Contact Information for Business Card

Dale Morven | Co-Founder |Managing Director
Suite 718 240 Wattlebrook Lane Melbourne Vic 3000

ABN 38 614 207 923
Tel: +61 0487 259 318 | Email: dale.morven@plivorantu.com

Font styles to use
Decorative
Script

Requirements
Must have
• Try few different design and some round corner business card
Should not have
• One round corner business card...try 4 different colour background not only black, make sure two side is designed. Be creative so imagine you are giving this to a client make sure has wow factor, if you can also try one design with engrave like all the logo, words look 3d feel
• The word Advertising Platform use attached file font

```html
<!DOCTYPE html>
<html lang="en">
<head>
<meta charset="utf-8">
<title>Tallyway Hub – Business Card</title>
<link href="https://fonts.googleapis.com/css2?family=Open+Sans:wght@400;600&display=swap" rel="stylesheet">
<style>
  :root {
    --stage: #2b2624;
    --card: #141414;
    --card-edge: #1d1d1d;
    --emboss: #3a3a3a;
    --muted: #8c8c8c;
    --ink: #f2f2f2;
    --accent-red: #e8452c;
    --accent-teal: #2fe0b0;
    --brand-orange: #f07a3c;
  }
  * { box-sizing: border-box; margin: 0; padding: 0; }
  html, body {
    width: 1200px; height: 864px; overflow: hidden;
    background: var(--stage);
    font-family: "Open Sans", Arial, sans-serif;
  }
  .canvas { position: relative; width: 1200px; height: 864px; }

  .card {
    position: absolute;
    width: 520px; height: 298px;
    background: var(--card);
    border: 1px solid var(--card-edge);
    box-shadow: 0 18px 40px rgba(0,0,0,.55);
  }
  .card--back { left: 60px; top: 110px; }
  .card--front { left: 620px; top: 420px; }

  /* back side */
  .back-brand {
    position: absolute; left: 0; right: 0; top: 92px;
    display: flex; align-items: center; justify-content: center; gap: 14px;
  }
  .back-brand__dot { width: 30px; height: 30px; border-radius: 50%; background: var(--emboss); }
  .back-brand__name {
    font-size: 40px; font-weight: 600; color: var(--emboss); letter-spacing: 1px;
  }
  .back-web {
    position: absolute; left: 0; right: 0; top: 196px; text-align: center;
    font-size: 13px; letter-spacing: 5px; color: var(--muted);
  }

  /* front side */
  .front-brand {
    position: absolute; left: 28px; top: 0; width: 222px; height: 100%;
    display: flex; align-items: center; justify-content: center; gap: 10px;
  }
  .front-brand__dot { width: 22px; height: 22px; border-radius: 50%; background: var(--brand-orange); flex: none; }
  .front-brand__name { font-size: 27px; font-weight: 600; color: var(--brand-orange); white-space: nowrap; }

  .divider {
    position: absolute; left: 262px; top: 40px; width: 2px; height: 218px;
    background: linear-gradient(to bottom, transparent, #9a9a9a 30%, #9a9a9a 70%, transparent);
  }

  .contact { position: absolute; left: 282px; top: 44px; color: var(--ink); font-size: 12.5px; line-height: 17px; }
  .contact__name { color: var(--accent-red); font-weight: 600; font-size: 14px; text-transform: uppercase; }
  .contact__role { color: var(--accent-teal); font-size: 14px; line-height: 18px; text-transform: uppercase; margin-bottom: 6px; }
  .contact__line { display: flex; align-items: center; gap: 7px; }
  .contact__line svg { width: 11px; height: 11px; fill: var(--accent-red); flex: none; }
  .contact__gap { height: 4px; }
</style>
</head>
<body>
<main class="canvas">
  <section class="card card--back" aria-label="Business card back">
    <div class="back-brand">
      <span class="back-brand__dot"></span>
      <span class="back-brand__name">Tallyway Hub</span>
    </div>
    <p class="back-web">www.plivorantu.com</p>
  </section>

  <section class="card card--front" aria-label="Business card front">
    <div class="front-brand">
      <span class="front-brand__dot"></span>
      <span class="front-brand__name">Tallyway Hub</span>
    </div>
    <div class="divider"></div>
    <div class="contact">
      <p class="contact__name">Dale Morven</p>
      <p class="contact__role">Co-Founder<br>Managing Director</p>
      <p>Plivorantu</p>
      <p>ABN 38 614 207 923</p>
      <p>Suite 718 240 Wattlebrook Lane</p>
      <p>Melbourne Vic 3000</p>
      <div class="contact__gap"></div>
      <p class="contact__line">
        <svg viewBox="0 0 24 24" aria-hidden="true"><path d="M6.6 10.8a15.1 15.1 0 0 0 6.6 6.6l2.2-2.2a1 1 0 0 1 1-.25 11.4 11.4 0 0 0 3.6.6 1 1 0 0 1 1 1V20a1 1 0 0 1-1 1A17 17 0 0 1 3 4a1 1 0 0 1 1-1h3.5a1 1 0 0 1 1 1c0 1.25.2 2.45.57 3.57a1 1 0 0 1-.25 1z"/></svg>
        +61 0487 259 318
      </p>
      <p class="contact__line">
        <svg viewBox="0 0 24 24" aria-hidden="true"><path d="M2 5h20v14H2zm2 2v.5l8 5 8-5V7l-8 5z"/></svg>
        dale.morven@plivorantu.com
      </p>
    </div>
  </section>
</main>
</body>
</html>
```